Medical centre needs a business card

We are a medcial centre in Australia, needing a new business card. Our demographic is low working class families. We are going to be renovating our premises to modernise the look and also had a new logo done a few months ago representing quality and community, and now need to update our cards. It needs to be doubled sided, with logo and contact details on the front, and appointment details on the back. . Needs to be modern and simple, easy to read. <br/><br/>Name: Kindle Grove Medical Centre <br/>Address: 512 Parmley Rd (Cnr Parmley Rd & Osgood Creek Rd),<br/>Tindarra Court Shopping Centre, Marrowbank, SA 5172<br/>Ph: 08 8461 3072<br/>Tag line: Where your wellbeing comes first<br/>Website: www.kindlegrovemedicalcentre-example.com.au<br/>Online bookings also available<br/><br/>(On the back, to have 3 lines of appointments that can be written in.<br/>Day, date, time)<br/><br/>Your next appointment is on<br/>Can try “M T W Th F Sa Su _________________ at ____________ am/pm” or other combinations <br/>Please advise as soon as possible if unable to attend<br/>Cancellation fees apply if less than 2 hrs notice<br/>Online appointments available (please highlight this option by either by position, colour or font)

Target Market(s)

Lower social economic working class, young families to seniors

Industry/Entity Type

Medical Centre

Contact Information for Business Card

Kindle Grove Medical Centre
512 Parmley Rd (Cnr Parmley Rd & Osgood Creek Drive)
Tindarra Court Shopping Centre
Paralowie SA 5108
Ph: 08 8461 3072
www.kindlegrovemedicalcentre-example.com.au
Tagline line: where your wellbeing comes first
Back side is for appointments
Your next appointment is with Dr ______________
Day/date/time (Please give 3 lines of appointments)
Please advise as soon as possible if unable to attend
Cancellation fees apply if less than 2 hours notice
Online appointments available
Book online easily and conveniently (please highlight online appointments)

Font styles to use
Serif
Sans Serif

Colors

Designer to choose colors to be used in the design.

Requirements
Must have
• Modern and simple
• Easy to ready
• Induces a wellbeing feeling
• Incorporate our logo colours and feel from logo
• Induces feeling of stability and security
Nice to have
• Attract attention
• Pleasant to look at
• Feeling of innovation
Should not have
• Loud clashing colours
• Overly luxurious feeling
• Overly artistic

```html
<!DOCTYPE html>
<html lang="en">
<head>
<meta charset="utf-8">
<title>Kindle Grove Medical Centre – Business Card</title>
<link rel="stylesheet" href="https://fonts.googleapis.com/css2?family=Source+Sans+3:wght@400;600;700&display=swap">
<style>
  :root{
    --blue:#1668cf;
    --blue-deep:#2a48bd;
    --sky:#1f9de8;
    --green:#8cc63f;
    --ink:#1560c4;
    --paper:#ffffff;
    --backdrop:#e9edf2;
  }
  *{box-sizing:border-box;margin:0;padding:0}
  html,body{width:1200px;height:800px;overflow:hidden}
  body{
    background:var(--backdrop);
    font-family:"Source Sans 3",Arial,sans-serif;
    color:var(--ink);
    display:flex;align-items:center;justify-content:center;gap:40px;
  }
  .card{
    position:relative;width:560px;height:320px;background:var(--paper);
    overflow:hidden;box-shadow:0 8px 24px rgba(20,40,80,.18);
  }

  /* ---------- back: appointments ---------- */
  .back__edge{position:absolute;left:0;top:0;bottom:0;width:12px;background:var(--blue)}
  .back__corner{
    position:absolute;right:0;bottom:0;width:190px;height:150px;
    background:linear-gradient(135deg,var(--sky),var(--blue) 55%,var(--blue-deep));
    clip-path:polygon(100% 0,100% 100%,0 100%,35% 55%,70% 30%);
  }
  .back__body{position:absolute;left:34px;top:24px;right:30px;font-size:17px;font-weight:600}
  .row{display:flex;align-items:flex-end;gap:6px;margin-bottom:9px;white-space:nowrap}
  .fill{flex:1;border-bottom:1px solid var(--ink);height:16px}
  .fill--short{flex:0 0 120px}
  .days{display:flex;gap:16px;margin-bottom:10px}
  .day::before{content:"";display:inline-block;width:10px;height:10px;border:1.4px solid var(--ink);margin-right:5px}
  .bullet{width:10px;height:10px;border-radius:50%;background:var(--ink);align-self:center}
  .notice{font-size:15px;line-height:1.3;margin-top:6px}
  .online{
    display:inline-block;margin-top:10px;background:var(--blue);color:#fff;
    border-radius:14px;padding:4px 20px;font-size:14px;font-weight:700;letter-spacing:.06em;
  }

  /* ---------- front: brand & contact ---------- */
  .front__art{
    position:absolute;left:0;top:0;width:230px;height:320px;
    background:linear-gradient(160deg,var(--sky),var(--blue) 50%,var(--blue-deep));
    clip-path:polygon(0 0,100% 0,62% 38%,78% 62%,20% 100%,0 100%);
  }
  .front__band{position:absolute;right:0;top:0;bottom:0;width:40px;background:var(--blue)}
  .front__icons{position:absolute;right:8px;bottom:22px;display:flex;flex-direction:column;gap:10px}
  .front__icons svg{width:22px;height:22px;fill:none;stroke:#fff;stroke-width:2}
  .brand{position:absolute;left:250px;top:60px;display:flex;align-items:center;gap:10px}
  .brand__dot{width:22px;height:22px;border-radius:50%;background:var(--green)}
  .brand__name{font-size:26px;font-weight:700;line-height:1.05;color:var(--blue)}
  .tagline{position:absolute;left:282px;top:124px;font-size:13px;letter-spacing:.08em}
  .contact{position:absolute;right:58px;top:180px;text-align:right;line-height:1.3}
  .contact__phone{font-size:22px;font-weight:700}
  .contact__line{font-size:14px;font-weight:600}
  .contact__addr{font-size:12px;font-weight:600}
</style>
</head>
<body>

<section class="card back" aria-label="Appointment side">
  <div class="back__edge"></div>
  <div class="back__corner" role="img" aria-label="Layered blue square decoration"></div>
  <div class="back__body">
    <div class="row">Your next appointment is with: Dr. <span class="fill"></span></div>
    <div class="days">
      <span class="day">Mon</span><span class="day">Tue</span><span class="day">Wed</span><span class="day">Thu</span><span class="day">Fri</span><span class="day">Sat</span><span class="day">Sun</span>
    </div>
    <div class="row"><span class="bullet"></span>Date: <span class="fill"></span> Time: <span class="fill fill--short"></span> am/pm</div>
    <div class="row"><span class="bullet"></span>Date: <span class="fill"></span> Time: <span class="fill fill--short"></span> am/pm</div>
    <div class="row"><span class="bullet"></span>Date: <span class="fill"></span> Time: <span class="fill fill--short"></span> am/pm</div>
    <p class="notice">Please advise as soon as possible if unable to attend<br>Cancellation fees apply if less than 2 hours notice</p>
    <span class="online">ONLINE APPOINTMENTS AVAILABLE</span>
  </div>
</section>

<section class="card front" aria-label="Brand and contact side">
  <div class="front__art" role="img" aria-label="Layered blue square decoration"></div>
  <div class="front__band"></div>
  <div class="front__icons">
    <svg viewBox="0 0 24 24" aria-label="Phone"><path d="M5 3h4l2 5-2.5 1.5a11 11 0 0 0 6 6L16 13l5 2v4a2 2 0 0 1-2 2A17 17 0 0 1 3 5a2 2 0 0 1 2-2z"/></svg>
    <svg viewBox="0 0 24 24" aria-label="Email"><rect x="3" y="5" width="18" height="14" rx="1"/><path d="M3 6l9 7 9-7"/></svg>
    <svg viewBox="0 0 24 24" aria-label="Website"><circle cx="12" cy="12" r="9"/><path d="M3 12h18M12 3c3 3 3 15 0 18M12 3c-3 3-3 15 0 18"/></svg>
    <svg viewBox="0 0 24 24" aria-label="Address"><path d="M12 22s7-7 7-12a7 7 0 0 0-14 0c0 5 7 12 7 12z"/><circle cx="12" cy="10" r="2.5"/></svg>
  </div>
  <div class="brand">
    <span class="brand__dot"></span>
    <span class="brand__name">Kindle Grove<br>Medical Centre</span>
  </div>
  <p class="tagline">Where your wellbeing comes first</p>
  <div class="contact">
    <p class="contact__phone">08 8461 3072</p>
    <p class="contact__line">hello@kindlegrove-example.com.au</p>
    <p class="contact__line">www.kindlegrovemedicalcentre-example.com.au</p>
    <p class="contact__addr">512 Parmley Rd (Cnr Parmley Rd &amp; Osgood Creek Drive)<br>Tindarra Court Shopping Centre, Marrowbank, SA 5172</p>
  </div>
</section>

</body>
</html>
```